Business Card for Coastal Tundrabridge Advisory

We need a business card for Coastal Tundrabridge Advisory. The company website address is provided below. The company logo is attached. We provide specialized permafrost services to the mining, transportation, and oil & gas industries. The card should be prepared for:
Matthias Korhonen, PhD.
Coastal Tundrabridge Advisory
PO Box 418259
Quillwater, Alaska 99642
Direct: +1-907-555-0143
Email: mkorhonen@tundrabridgeadvisory.example
Website: www.coastaltundrabridgeadvisory.example

```html
<!DOCTYPE html>
<html lang="en">
<head>
<meta charset="utf-8">
<title>Coastal Tundrabridge Advisory – Business Card</title>
<link rel="stylesheet" href="https://fonts.googleapis.com/css2?family=Montserrat:wght@400;500;600;700&display=swap">
<style>
  :root {
    --backdrop: #9a9a9a;
    --card: #ffffff;
    --ink: #111820;
    --ink-soft: #1c232b;
  }
  * { margin: 0; padding: 0; box-sizing: border-box; }
  html, body {
    width: 1093px; height: 1200px; overflow: hidden;
    background: var(--backdrop);
    font-family: "Montserrat", sans-serif;
    color: var(--ink);
  }
  .card {
    position: absolute;
    left: 265px;
    width: 580px;
    height: 348px;
    background: var(--card);
    border-radius: 16px;
  }
  .card--front { top: 225px; }
  .card--back { top: 616px; }

  .wordmark {
    font-weight: 600;
    text-transform: uppercase;
    color: var(--ink);
    text-align: center;
  }
  .card--front .wordmark {
    position: absolute;
    left: 52px; top: 190px;
    width: 182px;
    font-size: 13px;
    line-height: 1.25;
    letter-spacing: 1px;
  }
  .card--back .wordmark {
    position: absolute;
    left: 60px; right: 60px; top: 150px;
    font-size: 27px;
    line-height: 1.2;
    letter-spacing: 3px;
  }

  .divider {
    position: absolute;
    left: 241px; top: 121px;
    width: 1.5px; height: 167px;
    background: var(--ink);
  }
  .details {
    position: absolute;
    left: 251px; top: 122px;
    color: var(--ink-soft);
  }
  .details__name {
    font-size: 19px; font-weight: 700;
    line-height: 22px; color: var(--ink);
  }
  .details__title {
    font-size: 12.5px; font-weight: 500; line-height: 16px;
  }
  .details__address {
    margin-top: 12px;
    font-size: 13px; line-height: 16.5px; padding-left: 2px;
  }
  .contact { list-style: none; margin-top: 12px; }
  .contact__item {
    display: flex; align-items: center;
    height: 25.5px;
    font-size: 12.5px; font-weight: 500;
  }
  .contact__icon {
    width: 14px; height: 14px; margin: 0 9px 0 2px;
    flex: none;
  }
</style>
</head>
<body>
  <section class="card card--front" aria-label="Business card front">
    <div class="wordmark">Coastal Tundrabridge Advisory</div>
    <div class="divider"></div>
    <div class="details">
      <p class="details__name">Matthias Korhonen, PhD.</p>
      <p class="details__title">Managing Director</p>
      <p class="details__address">PO Box 418259<br>Quillwater, Alaska 99642</p>
      <ul class="contact">
        <li class="contact__item">
          <svg class="contact__icon" viewBox="0 0 24 24" aria-hidden="true"><path fill="#111820" d="M6.6 10.8a15.1 15.1 0 0 0 6.6 6.6l2.2-2.2a1 1 0 0 1 1-.25 11.4 11.4 0 0 0 3.6.57 1 1 0 0 1 1 1V20a1 1 0 0 1-1 1A17 17 0 0 1 3 4a1 1 0 0 1 1-1h3.5a1 1 0 0 1 1 1c0 1.25.2 2.45.57 3.57a1 1 0 0 1-.25 1z"/><path fill="none" stroke="#111820" stroke-width="2" d="M14 2.5a8 8 0 0 1 7.5 7.5M14 6a4.5 4.5 0 0 1 4 4"/></svg>
          +1-907-555-0143
        </li>
        <li class="contact__item">
          <svg class="contact__icon" viewBox="0 0 24 24" aria-hidden="true"><rect x="2" y="5" width="20" height="14" rx="1.5" fill="#111820"/><path d="M3 6l9 7 9-7" fill="none" stroke="#fff" stroke-width="1.6"/></svg>
          mkorhonen@tundrabridgeadvisory.example
        </li>
        <li class="contact__item">
          <svg class="contact__icon" viewBox="0 0 24 24" aria-hidden="true"><circle cx="12" cy="12" r="10" fill="#111820"/><path d="M12 2a10 10 0 0 1 0 20M2 12h20M12 2c-3 3-3 17 0 20M12 2c3 3 3 17 0 20" fill="none" stroke="#fff" stroke-width="1.2"/></svg>
          www.coastaltundrabridgeadvisory.example
        </li>
      </ul>
    </div>
  </section>

  <section class="card card--back" aria-label="Business card back">
    <div class="wordmark">Coastal Tundrabridge Advisory</div>
  </section>
</body>
</html>
```